Internal web page of multinational company - Portfolio of reports

We need to improve the look & feel of an existing internal HTML page.
We use it as a portfolios where users go and see a list of existing reports as "tiles". The HTML page is automatically generated by a javascript that reads the contents to display from an HTML file.
What is needs is a "face lift" in the design of the page.
Currently we use icons on the top right of each tile to denote the type of technology used on the report and also colons for the same purpose. The attached screenshots will be self explanatory.
Across the top we have "tabs" that, once selected change the tiles.
Need a proposal for new design that keeps is as clean as possible, specially the home page that should be very light (Plimbo like).
The idea for this page is to serve as a "one stop shop" and become a bookmark for everyone in the company.
Looking for a wow effect that make is visually

Target Market(s)

Internal employees

Industry/Entity Type

It Company

Coding

Coded - Design and coding required

Number of Pages Required

2 page

Requirements
Must have
• Should not change the logo or its position from the bottom left.
• Page must be as clean as possible and
Nice to have
• Welcome to change the logo on the top left. This page is from the CSU M&I (Mni) which stands for Central Support Unit - Metrics & Insight.
Should not have
• Do no use red, this is the color of our competitor. The blue on the bottom is standard for our logo

```html
<!DOCTYPE html>
<html lang="en">
<head>
<meta charset="utf-8">
<title>CSU M&amp;I – Report Portfolio</title>
<link href="https://fonts.googleapis.com/css2?family=Arimo:wght@400;700&display=swap" rel="stylesheet">
<style>
  :root {
    --header-top: #0a5cb0;
    --header-bottom: #003e8c;
    --page-bg: #eeeeee;
    --panel-bg: #f9f9f9;
    --tile-top: #ffffff;
    --tile-bottom: #ececec;
    --tile-border: #dcdcdc;
    --title-blue: #0b72b5;
    --brand-blue: #1d4f9c;
    --brand-dot: #9dbbe6;
    --icon-grey: #555a60;
    --search-bg: #0d4f9a;
    --filter-bg: #002f6c;
    --help-orange: #f7890f;
    --white: #ffffff;
  }
  * { box-sizing: border-box; margin: 0; padding: 0; }
  html, body { width: 1200px; height: 780px; overflow: hidden; }
  body {
    font-family: "Arimo", Arial, sans-serif;
    background: var(--page-bg);
    position: relative;
  }

  /* Header */
  .site-header {
    position: absolute; left: 0; top: 0; width: 1200px; height: 99px;
    background: linear-gradient(180deg, var(--header-top), var(--header-bottom));
  }
  .site-logo {
    position: absolute; left: 74px; top: 30px;
    display: flex; align-items: center; gap: 8px;
    color: var(--white); font-size: 30px; font-weight: 700; letter-spacing: 0.5px;
  }
  .site-logo .mark {
    width: 36px; height: 36px; border-radius: 50%; background: #3f8de0;
  }
  .main-nav {
    position: absolute; top: 42px; left: 293px;
    display: flex; align-items: center; gap: 14px;
  }
  .main-nav a {
    white-space: nowrap; color: var(--white);
    font-size: 12px; text-decoration: none;
    display: flex; align-items: center;
  }
  .main-nav a.section { font-weight: 700; }
  .main-nav a.section svg { margin-left: 5px; }
  .filter-button {
    position: absolute; left: 865px; top: 37px; width: 25px; height: 25px;
    border-radius: 50%; background: var(--filter-bg);
    display: flex; align-items: center; justify-content: center;
  }
  .search-box {
    position: absolute; left: 905px; top: 34px; width: 167px; height: 31px;
    background: var(--search-bg); border-radius: 2px;
    display: flex; align-items: center; justify-content: space-between;
    padding: 0 10px; color: var(--white); font-size: 12.5px;
  }

  /* Report panel */
  .report-panel {
    position: absolute; left: 127px; top: 157px; width: 945px; height: 487px;
    background: var(--panel-bg);
    border-bottom: 4px solid #d6d6d6;
    box-shadow: 0 1px 2px rgba(0,0,0,0.06);
  }
  .tile-grid {
    position: absolute; left: 15px; top: 39px;
    display: grid; grid-template-columns: repeat(4, 222px);
    column-gap: 10px; row-gap: 13px;
  }
  .report-tile {
    height: 85px;
    background: linear-gradient(180deg, var(--tile-top), var(--tile-bottom));
    border: 1px solid var(--tile-border); border-radius: 2px;
    position: relative;
  }
  .report-title {
    position: absolute; left: 13px; top: 19px;
    display: flex; align-items: center; gap: 5px;
    color: var(--title-blue); font-size: 11.6px; white-space: nowrap;
  }
  .report-title .bullet {
    width: 10px; height: 10px; border-radius: 50%; background: #9a9ea3;
    display: flex; align-items: center; justify-content: center;
  }
  .tech-brand {
    position: absolute; left: 13px; top: 52px;
    display: flex; align-items: center; gap: 4px;
    color: var(--brand-blue); font-size: 12px;
  }
  .tech-brand .dot { width: 14px; height: 14px; border-radius: 50%; background: var(--brand-dot); }
  .tile-actions {
    position: absolute; right: 9px; top: 55px;
    display: flex; gap: 9px; align-items: center;
  }

  /* Footer */
  .site-footer {
    position: absolute; left: 0; top: 688px; width: 1200px; height: 92px;
    background: linear-gradient(180deg, var(--header-top), var(--header-bottom));
  }
  .help-button {
    position: absolute; left: 128px; top: 34px; width: 125px; height: 31px;
    background: var(--help-orange); border-radius: 4px;
    color: var(--white); font-weight: 700; font-size: 14.5px;
    display: flex; align-items: center; justify-content: center;
  }
  .help-button svg { position: absolute; left: 70px; top: 30px; }
  .company-name {
    position: absolute; left: 962px; top: 44px;
    color: var(--white); font-weight: 700; font-size: 18px;
  }
  .page-code {
    position: absolute; left: 1149px; top: 46px;
    color: var(--white); font-size: 11px;
  }
</style>
</head>
<body>

<header class="site-header">
  <div class="site-logo"><span class="mark"></span>CSU M&amp;I</div>
  <nav class="main-nav">
    <a class="section">FINANCE<svg width="8" height="5" viewBox="0 0 8 5"><path d="M1 1l3 3 3-3" stroke="#fff" stroke-width="1.4" fill="none"/></svg></a>
    <a>GM View</a>
    <a>Hub View</a>
    <a>MI</a>
    <a class="section">GENERAL ACCOUNTING<svg width="8" height="5" viewBox="0 0 8 5"><path d="M1 1l3 3 3-3" stroke="#fff" stroke-width="1.4" fill="none"/></svg></a>
    <a>Tax</a>
    <a>Treasury</a>
    <a>Knowledge</a>
  </nav>
  <div class="filter-button">
    <svg width="10" height="10" viewBox="0 0 10 10"><path d="M0 0h10L6 5v5L4 8V5z" fill="#3f9be8"/></svg>
  </div>
  <div class="search-box">Search
    <svg width="12" height="12" viewBox="0 0 12 12"><circle cx="5" cy="5" r="3.6" stroke="#fff" stroke-width="1.8" fill="none"/><path d="M7.6 7.6L11 11" stroke="#fff" stroke-width="2"/></svg>
  </div>
</header>

<svg width="0" height="0" style="position:absolute">
  <defs>
    <g id="icon-wrench"><path d="M10 1.5a3 3 0 0 0-3.6 3.8L1 10.7 2.3 12l5.4-5.4A3 3 0 0 0 11.5 3L9.7 4.8 8.3 4.6 8.1 3.2z" fill="#555a60"/></g>
    <g id="icon-chart"><path d="M1 1v11h12" stroke="#555a60" stroke-width="1.3" fill="none"/><rect x="3.5" y="5" width="1.6" height="6" fill="#555a60"/><rect x="6.3" y="3" width="1.6" height="8" fill="#555a60"/><rect x="9.1" y="6" width="1.6" height="5" fill="#555a60"/></g>
    <g id="icon-doc"><path d="M2 0.5h6l3 3v9H2z" fill="#555a60"/><path d="M4 6h5M4 8h5M4 10h5" stroke="#eee" stroke-width="0.9"/></g>
    <g id="icon-chevron"><path d="M4 2.5l2.5 2.5L4 7.5" stroke="#fff" stroke-width="1.4" fill="none"/></g>
  </defs>
</svg>

<main class="report-panel">
  <div class="tile-grid">
    <article class="report-tile"><div class="report-title"><span class="bullet"><svg width="10" height="10" viewBox="0 0 10 10"><use href="#icon-chevron"/></svg></span>B &amp; AT Revenue &amp; Margin Analysis</div><div class="tech-brand"><span class="dot"></span>Tidewell</div><div class="tile-actions"><svg width="13" height="13"><use href="#icon-wrench"/></svg><svg width="14" height="13"><use href="#icon-chart"/></svg><svg width="12" height="13"><use href="#icon-doc"/></svg></div></article>
    <article class="report-tile"><div class="report-title"><span class="bullet"><svg width="10" height="10" viewBox="0 0 10 10"><use href="#icon-chevron"/></svg></span>B &amp; AT Revenue &amp; Margin Analysis</div><div class="tech-brand"><span class="dot"></span>Tidewell</div><div class="tile-actions"><svg width="13" height="13"><use href="#icon-wrench"/></svg><svg width="14" height="13"><use href="#icon-chart"/></svg><svg width="12" height="13"><use href="#icon-doc"/></svg></div></article>
    <article class="report-tile"><div class="report-title"><span class="bullet"><svg width="10" height="10" viewBox="0 0 10 10"><use href="#icon-chevron"/></svg></span>B &amp; AT Revenue &amp; Margin Analysis</div><div class="tech-brand"><span class="dot"></span>Tidewell</div><div class="tile-actions"><svg width="13" height="13"><use href="#icon-wrench"/></svg><svg width="14" height="13"><use href="#icon-chart"/></svg><svg width="12" height="13"><use href="#icon-doc"/></svg></div></article>
    <article class="report-tile"><div class="report-title"><span class="bullet"><svg width="10" height="10" viewBox="0 0 10 10"><use href="#icon-chevron"/></svg></span>B &amp; AT Revenue &amp; Margin Analysis</div><div class="tech-brand"><span class="dot"></span>Tidewell</div><div class="tile-actions"><svg width="13" height="13"><use href="#icon-wrench"/></svg><svg width="14" height="13"><use href="#icon-chart"/></svg><svg width="12" height="13"><use href="#icon-doc"/></svg></div></article>
    <article class="report-tile"><div class="report-title"><span class="bullet"><svg width="10" height="10" viewBox="0 0 10 10"><use href="#icon-chevron"/></svg></span>B &amp; AT Revenue &amp; Margin Analysis</div><div class="tech-brand"><span class="dot"></span>Tidewell</div><div class="tile-actions"><svg width="13" height="13"><use href="#icon-wrench"/></svg><svg width="14" height="13"><use href="#icon-chart"/></svg><svg width="12" height="13"><use href="#icon-doc"/></svg></div></article>
    <article class="report-tile"><div class="report-title"><span class="bullet"><svg width="10" height="10" viewBox="0 0 10 10"><use href="#icon-chevron"/></svg></span>B &amp; AT Revenue &amp; Margin Analysis</div><div class="tech-brand"><span class="dot"></span>Tidewell</div><div class="tile-actions"><svg width="13" height="13"><use href="#icon-wrench"/></svg><svg width="14" height="13"><use href="#icon-chart"/></svg><svg width="12" height="13"><use href="#icon-doc"/></svg></div></article>
    <article class="report-tile"><div class="report-title"><span class="bullet"><svg width="10" height="10" viewBox="0 0 10 10"><use href="#icon-chevron"/></svg></span>B &amp; AT Revenue &amp; Margin Analysis</div><div class="tech-brand"><span class="dot"></span>Tidewell</div><div class="tile-actions"><svg width="13" height="13"><use href="#icon-wrench"/></svg><svg width="14" height="13"><use href="#icon-chart"/></svg><svg width="12" height="13"><use href="#icon-doc"/></svg></div></article>
    <article class="report-tile"><div class="report-title"><span class="bullet"><svg width="10" height="10" viewBox="0 0 10 10"><use href="#icon-chevron"/></svg></span>B &amp; AT Revenue &amp; Margin Analysis</div><div class="tech-brand"><span class="dot"></span>Tidewell</div><div class="tile-actions"><svg width="13" height="13"><use href="#icon-wrench"/></svg><svg width="14" height="13"><use href="#icon-chart"/></svg><svg width="12" height="13"><use href="#icon-doc"/></svg></div></article>
    <article class="report-tile"><div class="report-title"><span class="bullet"><svg width="10" height="10" viewBox="0 0 10 10"><use href="#icon-chevron"/></svg></span>B &amp; AT Revenue &amp; Margin Analysis</div><div class="tech-brand"><span class="dot"></span>Tidewell</div><div class="tile-actions"><svg width="13" height="13"><use href="#icon-wrench"/></svg><svg width="14" height="13"><use href="#icon-chart"/></svg><svg width="12" height="13"><use href="#icon-doc"/></svg></div></article>
    <article class="report-tile"><div class="report-title"><span class="bullet"><svg width="10" height="10" viewBox="0 0 10 10"><use href="#icon-chevron"/></svg></span>B &amp; AT Revenue &amp; Margin Analysis</div><div class="tech-brand"><span class="dot"></span>Tidewell</div><div class="tile-actions"><svg width="13" height="13"><use href="#icon-wrench"/></svg><svg width="14" height="13"><use href="#icon-chart"/></svg><svg width="12" height="13"><use href="#icon-doc"/></svg></div></article>
    <article class="report-tile"><div class="report-title"><span class="bullet"><svg width="10" height="10" viewBox="0 0 10 10"><use href="#icon-chevron"/></svg></span>B &amp; AT Revenue &amp; Margin Analysis</div><div class="tech-brand"><span class="dot"></span>Tidewell</div><div class="tile-actions"><svg width="13" height="13"><use href="#icon-wrench"/></svg><svg width="14" height="13"><use href="#icon-chart"/></svg><svg width="12" height="13"><use href="#icon-doc"/></svg></div></article>
    <article class="report-tile"><div class="report-title"><span class="bullet"><svg width="10" height="10" viewBox="0 0 10 10"><use href="#icon-chevron"/></svg></span>B &amp; AT Revenue &amp; Margin Analysis</div><div class="tech-brand"><span class="dot"></span>Tidewell</div><div class="tile-actions"><svg width="13" height="13"><use href="#icon-wrench"/></svg><svg width="14" height="13"><use href="#icon-chart"/></svg><svg width="12" height="13"><use href="#icon-doc"/></svg></div></article>
    <article class="report-tile"><div class="report-title"><span class="bullet"><svg width="10" height="10" viewBox="0 0 10 10"><use href="#icon-chevron"/></svg></span>B &amp; AT Revenue &amp; Margin Analysis</div><div class="tech-brand"><span class="dot"></span>Tidewell</div><div class="tile-actions"><svg width="13" height="13"><use href="#icon-wrench"/></svg><svg width="14" height="13"><use href="#icon-chart"/></svg><svg width="12" height="13"><use href="#icon-doc"/></svg></div></article>
    <article class="report-tile"><div class="report-title"><span class="bullet"><svg width="10" height="10" viewBox="0 0 10 10"><use href="#icon-chevron"/></svg></span>B &amp; AT Revenue &amp; Margin Analysis</div><div class="tech-brand"><span class="dot"></span>Tidewell</div><div class="tile-actions"><svg width="13" height="13"><use href="#icon-wrench"/></svg><svg width="14" height="13"><use href="#icon-chart"/></svg><svg width="12" height="13"><use href="#icon-doc"/></svg></div></article>
  </div>
</main>

<footer class="site-footer">
  <div class="help-button">Help &amp; Feeback
    <svg width="14" height="10" viewBox="0 0 14 10"><path d="M0 0h14L12 10z" fill="#f7890f"/></svg>
  </div>
  <div class="company-name">Meridane</div>
  <div class="page-code">C5</div>
</footer>

</body>
</html>
```